KAJU Freightways #ALLKAJU Business Cards & Letterhead

I am looking to business cards designed for our organization. We are currently undergoing a small re-branding that is taking place. Our organization is called KAJU Freightways and we are headquartered in Phoenix, AZ. We primarily provide transportation and logistics services to the Marlow Parcel Bureau who is our largest customer. I would like to see a design that incorporates name, title, contact info, website, and address (this will be different depending on the employee). I would also like to see some color on the business card using our logo colors or a variation. I would like our logo on the back of the business card with the website displayed. The final design should communicate that we are a next generation transportation operate that focuses on being driver-first, customer-centric, innovative, and sustainable.We would also like our #ALLKAJU catch phrase incorporated as well.

Target Market(s)

Transportation & Logistics

Industry/Entity Type

Trucking Company

Contact Information for Business Card

-First and Last Name
-Position Title
-Contact Phone
-Contact Email
-Physical Address

Font styles to use
Serif

Colors

Designer to choose colors to be used in the design.

Requirements
Must have
• -KAJU logo prominently displayed
• -#ALLKAJU catch phrase used
• -Some amount of color, design gradient, etc.
• -Logo on the back with website listed (https://www.kajufreightco.example)

```html
<!DOCTYPE html>
<html lang="en">
<head>
<meta charset="utf-8">
<title>KAJU Freightways Business Card</title>
<link rel="stylesheet" href="https://fonts.googleapis.com/css2?family=Roboto+Slab:wght@400;700&display=swap">
<style>
  :root {
    --backdrop: #3a3b3d;
    --card: #202123;
    --card-dark: #1a1b1d;
    --teal: #063f4c;
    --green: #7cc320;
    --band: #2f3134;
    --white: #ffffff;
    --soft: #c9cacc;
    --emboss: #55575b;
  }
  * { box-sizing: border-box; margin: 0; padding: 0; }
  html, body { width: 799px; height: 1200px; overflow: hidden; }
  body {
    background: var(--backdrop);
    font-family: "Roboto Slab", Georgia, serif;
    position: relative;
  }
  .card {
    position: absolute;
    left: 80px;
    width: 640px;
    height: 366px;
    background: var(--card);
    overflow: hidden;
    box-shadow: 0 14px 30px rgba(0,0,0,.45);
  }
  .card--front { top: 140px; background: var(--card-dark); }
  .card--back { top: 694px; }

  .wordmark {
    position: absolute;
    display: flex;
    align-items: center;
    gap: 14px;
  }
  .wordmark__name {
    font-weight: 700;
    letter-spacing: 2px;
    line-height: 1;
  }
  .wordmark__dot {
    border-radius: 50%;
    border: 4px solid currentColor;
  }
  .card--front .wordmark {
    left: 50%; top: 112px; transform: translateX(-50%);
    color: var(--emboss);
  }
  .card--front .wordmark__name { font-size: 74px; }
  .card--front .wordmark__dot { width: 30px; height: 30px; }

  .front-url {
    position: absolute;
    left: 0; right: 0; top: 262px;
    display: flex; justify-content: center; align-items: center; gap: 20px;
    color: var(--soft);
    font-size: 14px;
    letter-spacing: 4px;
  }
  .front-url__dash { width: 34px; height: 3px; background: var(--green); }

  .back-art { position: absolute; inset: 0; }
  .person {
    position: absolute; left: 28px; top: 16px; color: var(--white);
  }
  .person__name { font-size: 21px; font-weight: 700; }
  .person__title { font-size: 12px; margin-top: 2px; }
  .tagline {
    position: absolute; left: 40px; top: 128px;
    color: var(--green); font-size: 14px; font-weight: 700;
  }
  .address {
    position: absolute; left: 40px; top: 154px;
    color: var(--white); font-size: 13px; line-height: 1.4;
  }
  .contacts {
    position: absolute; left: 40px; top: 208px;
    list-style: none; color: var(--white); font-size: 13px;
  }
  .contacts li { display: flex; align-items: center; gap: 10px; height: 22px; }
  .contacts svg { width: 13px; height: 13px; fill: var(--green); }
  .hashtag {
    position: absolute; left: 40px; top: 300px;
    color: var(--green); font-size: 15px; font-weight: 700; letter-spacing: 1px;
  }
  .card--back .wordmark { left: 392px; top: 244px; color: var(--white); }
  .card--back .wordmark__name { font-size: 58px; }
  .card--back .wordmark__dot { width: 26px; height: 26px; color: var(--green); }
</style>
</head>
<body>

<section class="card card--front" aria-label="Card front">
  <div class="wordmark">
    <span class="wordmark__name">KAJU</span>
    <span class="wordmark__dot"></span>
  </div>
  <p class="front-url">
    <span class="front-url__dash"></span>
    www.kajufreightco.example
    <span class="front-url__dash"></span>
  </p>
</section>

<section class="card card--back" aria-label="Card back">
  <svg class="back-art" viewBox="0 0 640 366" width="640" height="366" aria-hidden="true">
    <path fill="var(--teal)" d="M0 0H640V220C575 160 450 135 320 128C190 122 70 105 0 72Z"/>
    <path fill="var(--band)" d="M0 72C70 105 190 122 320 128C450 135 575 160 640 220V250C575 185 450 160 320 152C190 146 70 128 0 96Z"/>
    <path fill="none" stroke="var(--green)" stroke-width="6" d="M0 80C70 112 190 128 320 134C450 141 575 168 640 230"/>
    <path fill="none" stroke="var(--green)" stroke-width="3" d="M380 128C480 132 580 160 640 200"/>
  </svg>

  <div class="person">
    <h1 class="person__name">Dorian Vasquell</h1>
    <p class="person__title">Chairman &amp; CEO</p>
  </div>

  <p class="tagline">Transportation &amp; Energy Services</p>
  <p class="address">4120 North Cactus Ridge Road<br>Phoenix, AZ 85016</p>

  <ul class="contacts">
    <li><svg viewBox="0 0 24 24"><path d="M6.6 10.8a15 15 0 0 0 6.6 6.6l2.2-2.2c.3-.3.7-.4 1-.2 1.1.4 2.3.6 3.6.6.6 0 1 .4 1 1V20c0 .6-.4 1-1 1A17 17 0 0 1 3 4c0-.6.4-1 1-1h3.5c.6 0 1 .4 1 1 0 1.3.2 2.5.6 3.6.1.3 0 .7-.2 1z"/></svg>602-555-0148</li>
    <li><svg viewBox="0 0 24 24"><path d="M2 5h20v14H2zm2 2v.5l8 5 8-5V7l-8 5z"/></svg>dorian@kajufreightco.example</li>
    <li><svg viewBox="0 0 24 24"><circle cx="12" cy="12" r="10"/></svg>www.kajufreightco.example</li>
  </ul>

  <p class="hashtag">#ALLKAJU</p>

  <div class="wordmark">
    <span class="wordmark__name">KAJU</span>
    <span class="wordmark__dot"></span>
  </div>
</section>

</body>
</html>
```